Business card for Eyelash extension salon in Beverly Hills,California USA

We need new business card for our salon in Beverly Hills. The salon name is 'Lashvera' . We would like to have...Business name: Lashvera Name of person: will provide later Address 4720 N.Alder Crest Ave Beverly Hills , CA 90210 Phone: will provide later (Text only) Web: www.lashverastudio.example Snapgrid icon, Circlebook icon follow us for seasonal campaign and news @lashverastudiolounge Design should look elegant, high-end, clean, simple, cohesive with my brand. Please refer my brand board. Business name color will be metallic bronzy color. Im thinking grey background or white background. Thanks

Target Market(s)

25-35. Gender neutral. People who are in Entertainment business industry.
This is High-end Eyelash extension salon in Beverly Hills

Industry/Entity Type

Beauty Salon

Contact Information for Business Card

Business name: Lashvera
Name of person: will provide later
Address 4720 N.Alder Crest Ave Beverly Hills , CA 90210
Phone: will provide later (Text only)
Web: www.lashverastudio.example
Snapgrid icon, Circlebook icon
follow us for seasonal campaign and news @lashverastudiolounge

Requirements
Must have
• Beautiful, elegant, clean and simple look but very attractive and modern
Should not have
• We don't like too clutter, too busy designs.

```html
<!DOCTYPE html>
<html lang="en">
<head>
<meta charset="utf-8">
<title>Lashvera Business Card</title>
<link href="https://fonts.googleapis.com/css2?family=Playfair+Display:wght@400;600&family=Work+Sans:wght@400;600&display=swap" rel="stylesheet">
<style>
  :root {
    --backdrop: #1d1d1d;
    --paper: #ffffff;
    --bronze: #7d5840;
    --bronze-card: #8a6950;
    --divider: #a89080;
    --ink-light: #ffffff;
  }
  html, body {
    margin: 0;
    padding: 0;
    width: 1200px;
    height: 897px;
    overflow: hidden;
    background: var(--backdrop);
  }
  .canvas {
    position: relative;
    width: 1200px;
    height: 897px;
  }
  .card {
    position: absolute;
    left: 347px;
    width: 499px;
    height: 284px;
    box-shadow: 0 10px 30px rgba(0,0,0,0.55);
  }
  .card-front {
    top: 158px;
    background: var(--paper);
    color: var(--bronze);
  }
  .card-back {
    top: 465px;
    height: 285px;
    background: var(--bronze-card);
    color: var(--ink-light);
  }
  .wordmark {
    position: absolute;
    margin: 0;
    font-family: "Playfair Display", serif;
    font-weight: 400;
    line-height: 1;
    text-align: center;
    white-space: nowrap;
    transform: translate(-50%, -50%);
  }
  .card-front .wordmark {
    left: 261px;
    top: 80px;
    font-size: 44px;
  }
  .card-back .wordmark {
    left: 361px;
    top: 162px;
    font-size: 52px;
  }
  .person-name {
    position: absolute;
    left: 0;
    right: 0;
    top: 168px;
    text-align: center;
    font-family: "Playfair Display", serif;
    font-weight: 600;
    font-size: 22px;
    line-height: 26px;
    letter-spacing: 0.03em;
    margin: 0;
  }
  .contact-row {
    position: absolute;
    left: 17px;
    right: 18px;
    top: 231px;
    display: flex;
    justify-content: space-between;
    align-items: center;
    font-family: "Work Sans", sans-serif;
    font-size: 12px;
    line-height: 18px;
    letter-spacing: 0.03em;
    white-space: nowrap;
  }
  .contact-divider {
    color: var(--divider);
  }
  .social-handle {
    position: absolute;
    left: 71px;
    top: 204px;
    margin: 0;
    font-family: "Work Sans", sans-serif;
    font-weight: 600;
    font-size: 14px;
    line-height: 20px;
    white-space: nowrap;
  }
</style>
</head>
<body>
<main class="canvas">
  <section class="card card-front" aria-label="Business card front">
    <p class="wordmark">Lashvera</p>
    <h1 class="person-name">MARA ELLSWORTH</h1>
    <div class="contact-row">
      <span class="contact-phone">(555) 014 7788</span>
      <span class="contact-divider">|</span>
      <span class="contact-email">info@maraellsworth.example</span>
      <span class="contact-divider">|</span>
      <span class="contact-social">@lashverastudiolounge</span>
    </div>
  </section>

  <section class="card card-back" aria-label="Business card back">
    <p class="social-handle">@lashverastudiolounge</p>
    <p class="wordmark">Lashvera</p>
  </section>
</main>
</body>
</html>
```